Deskside Thrive Fliers and logo design

We need to design a product logo and some informational fliers for a vigour quest.
I have attached our Deskside Thrive logo - colours need to be complimentary but not the same, we would like fresh, funky but still professional. We generally communicate in a fairly casual way to reach our market. (We don't like boring)
Clear and simple - not too busy
images are good but not actual photos
Here is our website to give you an idea www.desksidethrive.co.nz
The flier is a 3 page document.
The logo is to say Vigour Quest. The challenge is based on exercise, connecting with people, giving, learning and taking notice (The 7 paths to flourishing) Once agin the logo needs to be complementary but not the same.
The Deskside thrive logo needs to be on the fliers but the vigour quest logo is separate.
Thanks very much!!

```html
<!DOCTYPE html>
<html lang="en">
<head>
<meta charset="utf-8">
<title>Deskside Thrive – Vigour Quest Fliers</title>
<link href="https://fonts.googleapis.com/css2?family=Oswald:wght@500;600&family=Open+Sans:wght@400;600;700&display=swap" rel="stylesheet">
<style>
  :root {
    --backdrop: #3b3b3b;
    --paper: #ffffff;
    --rust: #b6442b;
    --orange: #d9532c;
    --green: #3f9a7e;
    --green-dark: #2f7f67;
    --ink: #3a3a3a;
    --muted: #666666;
    --rule: #c9c9c9;
  }
  * { margin: 0; padding: 0; box-sizing: border-box; }
  html, body { width: 1200px; height: 900px; overflow: hidden; }
  body {
    background: radial-gradient(ellipse at 50% 40%, #4a4a4a 0%, var(--backdrop) 70%);
    font-family: "Open Sans", Arial, sans-serif;
    color: var(--ink);
    position: relative;
  }
  .page {
    position: absolute;
    top: 158px;
    width: 340px;
    height: 480px;
    background: var(--paper);
    overflow: hidden;
  }
  .page--intro { left: 68px; }
  .page--values { left: 437px; width: 338px; }
  .page--tips { left: 800px; }

  .footer-band {
    position: absolute; left: 0; right: 0; bottom: 0; height: 24px;
    background: var(--rust); color: #fff;
    font-family: "Open Sans", Arial, sans-serif; font-weight: 700;
    font-size: 9px; letter-spacing: 0.4px;
    display: flex; align-items: center; justify-content: flex-end; padding-right: 22px;
  }
  .page--values .footer-band { justify-content: center; padding: 0; }
  .pattern-band { position: absolute; left: 0; right: 0; height: 14px;
    background: linear-gradient(90deg, #f2c4b4, #cfe6dc, #f6d6a8, #f2c4b4, #cfe6dc, #f6d6a8); opacity: .8; }

  /* Page 1 */
  .intro-title {
    position: absolute; top: 24px; left: 0; right: 0; text-align: center;
    font-family: "Oswald", sans-serif; font-weight: 600; font-size: 31px; color: var(--rust); letter-spacing: 0.3px;
  }
  .intro-band {
    position: absolute; top: 68px; left: 126px; width: 192px; height: 24px;
    background: var(--green); color: #fff; text-align: center;
    font-family: "Oswald", sans-serif; font-weight: 500; font-size: 18px; line-height: 24px; letter-spacing: 0.4px;
  }
  .intro-photo {
    position: absolute; top: 92px; left: 0; width: 150px; height: 350px;
    background: linear-gradient(180deg, #f4f1ea 0%, #e7ecd8 55%, #a9c08a 85%, #7f9f5e 100%);
  }
  .intro-copy { position: absolute; top: 98px; left: 152px; width: 178px; }
  .intro-lead {
    font-weight: 700; font-size: 7.6px; line-height: 9.4px; color: var(--orange); text-align: right;
    padding: 3px 0; border-top: 1px dotted var(--green); border-bottom: 1px dotted var(--green);
  }
  .intro-copy p { font-size: 4.5px; line-height: 6px; color: var(--muted); margin-top: 6px; }
  .stop-list { position: absolute; top: 232px; left: 160px; width: 170px; list-style: none; }
  .stop-list li { display: flex; align-items: flex-start; gap: 4px; margin-bottom: 6px; font-size: 4.5px; line-height: 6px; color: var(--muted); }
  .stop-list .tick { flex: none; width: 7px; height: 7px; }
  .stop-key {
    flex: none; width: 40px; background: var(--orange); color: #fff;
    font-family: "Oswald", sans-serif; font-weight: 500; font-size: 7.5px; line-height: 10px; padding-left: 3px;
  }
  .stop-sub { display: grid; grid-template-columns: 20px 64px 10px 66px; gap: 4px; margin: -2px 0 6px 11px; font-size: 4.2px; line-height: 5.6px; color: var(--muted); }
  .stop-sub b { color: var(--orange); font-size: 3.6px; font-weight: 700; }
  .brand-mark { position: absolute; top: 350px; left: 196px; display: flex; align-items: center; gap: 5px; }
  .brand-mark__dot { width: 12px; height: 12px; border-radius: 50%; background: var(--green); }
  .brand-mark__name { font-weight: 600; font-size: 15px; line-height: 16px; color: var(--green); }

  /* Page 2 */
  .values-tag {
    position: absolute; top: 28px; left: 10px; background: var(--green); color: #fff;
    font-family: "Oswald", sans-serif; font-size: 9px; padding: 1px 14px 1px 6px; letter-spacing: .3px;
  }
  .values-intro { position: absolute; top: 46px; left: 16px; width: 310px; font-size: 7.2px; line-height: 9px; color: #222; }
  .section-head { font-family: "Oswald", sans-serif; font-weight: 500; font-size: 8px; color: var(--orange); letter-spacing: .3px; }
  .values-what { position: absolute; top: 67px; left: 16px; }
  .values-note { position: absolute; top: 81px; left: 16px; width: 310px; font-size: 4.2px; line-height: 5.6px; color: var(--muted); }
  .values-box {
    position: absolute; border: 1px solid var(--green-dark); padding: 5px 4px;
    display: grid; grid-template-columns: 1fr 1fr; column-gap: 4px;
  }
  .values-box ul { list-style: none; }
  .values-box li { position: relative; padding-left: 8px; font-size: 4.2px; line-height: 11px; font-weight: 600; color: #333; white-space: nowrap; }
  .values-box li::before {
    content: ""; position: absolute; left: 1px; top: 3px; width: 2px; height: 4px;
    border-right: 1.2px solid var(--green); border-bottom: 1.2px solid var(--green); transform: rotate(40deg);
  }
  .values-box li.cont::before { display: none; }
  .box-a { top: 103px; left: 14px; width: 150px; height: 165px; }
  .box-b { top: 103px; left: 168px; width: 160px; height: 165px; }
  .box-c { top: 272px; left: 14px; width: 150px; height: 166px; }
  .step { position: absolute; left: 172px; width: 156px; }
  .step-two { top: 274px; }
  .step-three { top: 380px; }
  .step p { font-size: 4.4px; line-height: 5.8px; color: var(--muted); margin-top: 3px; }
  .rank-list { list-style: none; margin-top: 5px; }
  .rank-list li { display: flex; align-items: center; gap: 4px; margin-bottom: 3px; }
  .rank-list span {
    width: 8px; height: 8px; border-radius: 50%; border: 0.8px solid var(--green);
    font-size: 4.5px; line-height: 7px; text-align: center; color: var(--green);
  }
  .rank-list i { flex: 1; border-bottom: 0.8px solid var(--rule); height: 4px; margin-right: 20px; }

  /* Page 3 */
  .tips-title {
    position: absolute; top: 24px; left: 0; right: 0; text-align: center;
    font-family: "Oswald", sans-serif; font-weight: 600; font-size: 16px; color: var(--orange); letter-spacing: .3px;
  }
  .tips-title span { color: var(--green); }
  .tips-callout {
    position: absolute; top: 52px; left: 22px; width: 296px; height: 34px;
    border: 1.2px solid var(--green-dark); border-radius: 8px;
    font-weight: 700; font-size: 5.6px; line-height: 7.4px; text-align: center; padding: 5px 10px; color: #222;
  }
  .tips-sub {
    position: absolute; top: 94px; left: 0; right: 0; text-align: center;
    font-family: "Oswald", sans-serif; font-weight: 500; font-size: 9px; color: var(--orange); letter-spacing: .3px;
  }
  .tips-list { position: absolute; top: 114px; left: 26px; width: 294px; list-style: none; }
  .tip { display: grid; grid-template-columns: 68px 14px 1fr; align-items: center; min-height: 24px; margin-bottom: 8.6px; }
  .tip h3 { font-weight: 700; font-size: 5.2px; line-height: 6.4px; color: var(--green); text-transform: uppercase; }
  .tip svg { width: 9px; height: 9px; }
  .tip p { font-size: 4.3px; line-height: 5.7px; color: #333; }
</style>
</head>
<body>

<svg width="0" height="0" style="position:absolute">
  <defs>
    <symbol id="tick" viewBox="0 0 10 10"><path d="M1.5 5.2 L4 8 L8.8 1.8" fill="none" stroke="#b6442b" stroke-width="1.8" stroke-linecap="round"/></symbol>
    <symbol id="arrow-dot" viewBox="0 0 10 10"><circle cx="5" cy="5" r="5" fill="#d9532c"/><path d="M2.6 5 H7 M5 3 L7.2 5 L5 7" stroke="#fff" stroke-width="1.1" fill="none"/></symbol>
  </defs>
</svg>

<!-- Page 1 -->
<section class="page page--intro">
  <h1 class="intro-title">PEOPLE WORK BETTER</h1>
  <div class="intro-band">WHEN THEY FEEL GOOD</div>
  <div class="intro-photo" role="img" aria-label="Illustration of a woman in a white dress, arms open, enjoying the sun in a green field"></div>
  <div class="intro-copy">
    <p class="intro-lead">We cannot control what happens to us in life<br>but we can change the way we react</p>
    <p>Stress happens because we are allowing fear, anger, disappointment and a host of other negative emotions to navigate our actions. By becoming aware of these emotions and allowing them to simply be, we can begin to gain control of how we react and respond to stressful situations.</p>
    <p>Our experience is always changing. Without awareness, mental patterns related to what we fear and what upsets us make life harder.</p>
    <p>S.T.O.P is a powerful, yet surprisingly basic strategy that helps you to be focused, alert, relaxed and at your emotional best when stressful moments present themselves in your life.</p>
    <p>Simply put, it's a four-step checklist to use anytime you want to ground yourself and get some insight into whatever is going on. The whole idea behind it is that by taking a very brief break—even less than one minute—you can determine the very best action to take in the moment.</p>
  </div>
  <ul class="stop-list">
    <li><svg class="tick"><use href="#tick"/></svg><span class="stop-key">S = STOP</span><span>Stop what you are doing: Press the pause button on your thoughts and actions.</span></li>
    <li><svg class="tick"><use href="#tick"/></svg><span class="stop-key">T = TAKE</span><span>Take a few deep breaths to centre yourself and bring yourself fully into the present moment.</span></li>
    <li><svg class="tick"><use href="#tick"/></svg><span class="stop-key">O = OBSERVE</span><span>Observe what is going on with you:</span></li>
    <li class="stop-sub"><b>BODY</b><span>What physical sensations are you aware of (touch, sight, hearing, taste, smell)?</span><b>MIND</b><span>What assumptions are you making about your feelings? What story are you telling yourself?</span></li>
    <li class="stop-sub"><b>EMOTIONS</b><span>What are you feeling right now?</span><b></b><span></span></li>
    <li><svg class="tick"><use href="#tick"/></svg><span class="stop-key">P = PROCEED</span><span>Proceed with whatever you were doing, making a conscious, intentional choice to incorporate what you just learned.</span></li>
  </ul>
  <div class="brand-mark">
    <span class="brand-mark__dot"></span>
    <span class="brand-mark__name">Deskside<br>thrive</span>
  </div>
  <footer class="footer-band">visit us-www.desksidethrive.co.nz</footer>
</section>

<!-- Page 2 -->
<section class="page page--values">
  <div class="pattern-band" style="top:0" role="img" aria-label="Decorative band of soft coloured leaf shapes"></div>
  <h2 class="values-tag">VALUES</h2>
  <p class="values-intro">This exercise is designed to help you reach a better understanding of your most significant values.</p>
  <h3 class="section-head values-what">WHAT I VALUE MOST…</h3>
  <p class="values-note">From this list of values (both work and personal), select the ten that are most important to you - as guides for how to behave, or as components of a valued way of life. Feel free to add any values of your own to this list</p>
  <div class="values-box box-a">
    <ul><li>Achievement</li><li>Advancement and promotion</li><li>Adventure</li><li>Affection (love and caring)</li><li>Arts</li><li>Challenging problems</li><li>Change and variety</li><li>Close relationships</li><li>Community</li><li>Competence</li><li>Competition</li><li>Cooperation</li><li>Country</li></ul>
    <ul><li>Creativity</li><li>Decisiveness</li><li>Democracy</li><li>Ecological awareness</li><li>Economic security</li><li>Effectiveness</li><li>Efficiency</li><li>Ethical practice</li><li>Excellence</li><li>Excitement</li><li>Fame</li><li>Fast living</li><li>Financial gain</li><li>Freedom</li></ul>
  </div>
  <div class="values-box box-b">
    <ul><li>ability</li><li>Physical challenge</li><li>Pleasure</li><li>Power and authority</li><li>Privacy</li><li>Public service</li><li>Purity</li><li>Quality of what I take part in</li><li>Quality relationships</li><li>Recognition (respect from</li><li class="cont">others, status)</li><li>Religion</li><li>Reputation</li><li>Responsibility and account</li></ul>
    <ul><li>Security</li><li>Self-Respect</li><li>Serenity</li><li>Sophistication</li><li>Stability</li><li>Status</li><li>Supervising others</li><li>Time freedom</li><li>Truth</li><li>Wealth</li><li>Wisdom</li><li>Work under pressure</li><li>Work with others</li><li>Working alone</li></ul>
  </div>
  <div class="values-box box-c">
    <ul><li>Friendships</li><li>Growth</li><li>Having a family</li><li>Helping other people</li><li>Helping society</li><li>Honesty</li><li>Independence</li><li>Influencing others</li><li>Inner harmony</li><li>Integrity</li><li>Intellectual status</li><li>Involvement</li><li>Job tranquility</li><li>Knowledge</li></ul>
    <ul><li>Leadership</li><li>Location</li><li>Loyalty</li><li>Market position</li><li>Meaningful work</li><li>Merit</li><li>Money</li><li>Nature</li><li>Being around people who</li><li>are open and honest</li><li>Order (tranquility,</li><li class="cont">stability, conformity)</li><li>Personal development</li></ul>
  </div>
  <div class="step step-two">
    <h3 class="section-head">STEP 2: ELIMINATION</h3>
    <p>Now that you have identified ten, imagine that you are only permitted to have five values. Which five would you give up? Cross them off. Put them into order, the one that is most important to you first. Write it somewhere and refer to it when you can't make a decision, align yourself with what makes you feel good.</p>
    <ol class="rank-list">
      <li><span>1</span><i></i></li><li><span>2</span><i></i></li><li><span>3</span><i></i></li><li><span>4</span><i></i></li><li><span>5</span><i></i></li>
    </ol>
  </div>
  <div class="step step-three">
    <h3 class="section-head">STEP 3: SUPPORT YOURSELF</h3>
    <p>Write it somewhere and refer to it when you can't make a decision, align yourself with what makes you feel good.</p>
  </div>
  <footer class="footer-band">visit us-www.desksidethrive.co.nz</footer>
</section>

<!-- Page 3 -->
<section class="page page--tips">
  <h2 class="tips-title">10 TIPS TO IMPROVE <span>YOUR WELLBEING</span></h2>
  <p class="tips-callout">Yes, you will have to get off the couch and you might need to say no to burgers for lunch every day but we promise we won't turn you into spandex wearing vegans with prescriptions to Glowhaus!</p>
  <h3 class="tips-sub">SMALL CHANGES EVERY DAY CAN MAKE A HUGE DIFFERENCE.</h3>
  <ul class="tips-list">
    <li class="tip"><h3>Put on your wake up grin</h3><svg><use href="#arrow-dot"/></svg><p>Smile and think happy thoughts – that first 90 secs has a big impact on your day. If you start the day with bad thoughts, then it compounds – simply turn up the corners of your mouth you'll start to release endorphins and serotonin, your feel-good hormones.</p></li>
    <li class="tip"><h3>Drink lemon and warm water first thing</h3><svg><use href="#arrow-dot"/></svg><p>Smile and think happy thoughts – that first 90 secs has a big impact on your day. If you start the day with bad thoughts, then it compounds – simply turn up the corners of your mouth you'll start to release endorphins and serotonin, your feel-good hormones.</p></li>
    <li class="tip"><h3>Exercise</h3><svg><use href="#arrow-dot"/></svg><p>It boosts the happy chemicals in your brain. So Be Active - get your heart rate going and stretch those muscles. At the very least take the stairs. To get your endorphins surging you'll need to really heavy breathe – so walk up those stairs faster, do your house work quicker – get that heart pumping.</p></li>
    <li class="tip"><h3>Eat a banana</h3><svg><use href="#arrow-dot"/></svg><p>Did you ever see a depressed chimp? Bananas help to lessen feelings of stress and anxiety due to high levels of tryptophan which converts to serotonin – one of those happy hormones. The high level of potassium helps you to be more alert and will give you energy.</p></li>
    <li class="tip"><h3>Put on your wow!</h3><svg><use href="#arrow-dot"/></svg><p>Go outside and Take Notice – The wind, the warmth, the cold, the trees, the blossom, the amazing sky, the moon. The world is full of things that make you go WOW, if you just slow down and Take Notice. Even better, go with a friend and Connect as well.</p></li>
    <li class="tip"><h3>5 fruit and veg per day</h3><svg><use href="#arrow-dot"/></svg><p>Get the fibre into to you… Without it you clog up, if you clog up you get grumpy and sluggish. If you get grumpy and sluggish – let's not go there! If you have trouble fitting the vegies in, put them into a smoothie</p></li>
    <li class="tip"><h3>Play music</h3><svg><use href="#arrow-dot"/></svg><p>It cheers you up. Create a playlist for when you need a pick-me-up. Play it in the car to and from work, doing your housework or when you're going for that brisk walk, getting out of breath and send even more happy hormones to your brain. (No, not the sad break-up playlist!)</p></li>
    <li class="tip"><h3>Remove a poison</h3><svg><use href="#arrow-dot"/></svg><p>Take away something that you know is bad for you – fast food, sugar, gluten – even for a couple of days a week – replace it with something healthy like water, fruit, veg, quinoa, exercise whatever works for you.</p></li>
    <li class="tip"><h3>Kill em with kindness</h3><svg><use href="#arrow-dot"/></svg><p>When you're feeling bad, do something nice for someone else and it will make their day and you'll feel even better. In fact, Give every day.</p></li>
    <li class="tip"><h3>Keep the cogs turning</h3><svg><use href="#arrow-dot"/></svg><p>Use it or lose it as they say – use your brain. Keep learning – something new every day.</p></li>
  </ul>
  <div class="pattern-band" style="bottom:0" role="img" aria-label="Decorative band of soft coloured leaf shapes"></div>
</section>

</body>
</html>
```